Eye-Catching Christian Book Series

Modern and edgy for men and women ages 18-35.
I’d like a fresh, bright and clean book cover that will be a series. The title should look like it’s own unique logo that I can use again like the “for starters” book series. I like turquoise, yellow, gray and white. (Open to all suggestions)
I think a picture with water would be nice.

Target Market(s)

New Christians,
Christians, Churches, Millennials, Gen Z

Font styles to use
Serif
Sans Serif

Colors
33b8a4
86cfc6
cfeae6
ffffff
fbee3e

Requirements
Must have
• The Title is “Fresh Dawn on the Narrow Path”
A subtitle “A First Walker’s Map”
Author’s Name: Renna Colvert

- The title “Fresh Dawn” should look like a logo so that I can use it for my other copyrighted books.
Nice to have
• Water, clean, new look

The title should look modern and look up to date. Like current 2020-2021 Book Covers
Should not have
• No red colors, no crosses

```html
<!DOCTYPE html>
<html lang="en">
<head>
<meta charset="utf-8">
<title>Fresh Dawn on the Narrow Path — Book Cover</title>
<link rel="stylesheet" href="https://fonts.googleapis.com/css2?family=Cinzel:wght@400;600&family=Kaushan+Script&display=swap">
<style>
  :root {
    --backdrop: #2f2f2f;
    --paper: #ffffff;
    --ink-gray: #545454;
    --ink-soft: #4a4a4a;
    --teal: #4cb5c2;
    --teal-deep: #3aa6b4;
    --rule: #9a9a9a;
    --shell-light: #e0b68a;
    --shell-dark: #a8673a;
    --leaf: #4f8a2a;
  }
  html, body {
    margin: 0;
    padding: 0;
    width: 1200px;
    height: 1200px;
    overflow: hidden;
    background: var(--backdrop);
  }
  .canvas {
    position: relative;
    width: 1200px;
    height: 1200px;
    background: var(--backdrop);
  }
  .cover {
    position: absolute;
    left: 214px;
    top: 22px;
    width: 772px;
    height: 1156px;
    background: var(--paper);
    font-family: "Cinzel", "Times New Roman", serif;
    color: var(--ink-gray);
  }
  .title-block {
    position: absolute;
    left: 0;
    top: 70px;
    width: 100%;
    text-align: center;
  }
  .title-main {
    margin: 0;
    font-weight: 600;
    font-size: 96px;
    line-height: 98px;
    letter-spacing: 1px;
    color: var(--ink-gray);
  }
  .title-connector {
    position: relative;
    height: 40px;
    margin-top: 6px;
  }
  .title-connector .rule {
    position: absolute;
    top: 20px;
    height: 2px;
  }
  .rule-left {
    left: 92px;
    width: 222px;
    background: linear-gradient(to right, rgba(154,154,154,0), var(--rule));
  }
  .rule-right {
    right: 92px;
    width: 222px;
    background: linear-gradient(to left, rgba(154,154,154,0), var(--rule));
  }
  .title-connector .word {
    position: absolute;
    left: 0;
    right: 0;
    top: 2px;
    font-size: 28px;
    font-weight: 600;
    letter-spacing: 2px;
    line-height: 36px;
  }
  .title-script {
    margin: 4px 0 0;
    font-family: "Kaushan Script", "Brush Script MT", cursive;
    font-weight: 400;
    font-size: 112px;
    line-height: 140px;
    color: var(--teal);
  }
  .cover-art {
    position: absolute;
    left: 250px;
    top: 530px;
    width: 260px;
    height: 360px;
  }
  .subtitle {
    position: absolute;
    left: 0;
    top: 942px;
    width: 100%;
    text-align: center;
    font-size: 24px;
    letter-spacing: 5px;
    color: var(--ink-soft);
    margin: 0;
  }
  .author {
    position: absolute;
    left: 0;
    top: 1060px;
    width: 100%;
    text-align: center;
    font-size: 50px;
    font-weight: 600;
    letter-spacing: 2px;
    color: var(--teal-deep);
    margin: 0;
  }
</style>
</head>
<body>
<div class="canvas">
  <div class="cover">
    <div class="title-block">
      <h1 class="title-main">FRESH<br>DAWN</h1>
      <div class="title-connector">
        <span class="rule rule-left"></span>
        <span class="word">ON THE</span>
        <span class="rule rule-right"></span>
      </div>
      <p class="title-script">Narrow Path</p>
    </div>

    <svg class="cover-art" viewBox="0 0 260 360" role="img" aria-label="Photo of a tiny boat made from a walnut shell with a green leaf sail on a toothpick mast">
      <defs>
        <radialGradient id="artTone" cx="50%" cy="55%" r="60%">
          <stop offset="0%" stop-color="#e8d2b6"/>
          <stop offset="55%" stop-color="#f3ebe0"/>
          <stop offset="100%" stop-color="#ffffff"/>
        </radialGradient>
      </defs>
      <rect width="260" height="360" fill="url(#artTone)"/>
    </svg>

    <p class="subtitle">A FIRST WALKER’S MAP</p>
    <p class="author">RENNA COLVERT</p>
  </div>
</div>
</body>
</html>
```